Business card design for a dynamic IT consulting company

We need a business card design for a young firm, specialized in the Telecommunications/Consulting industry. The name of the company is Quindor and Partners Business Consulting Ltd. (Short name: Quindor and Partnes)
Quindor = solve read reverse, so we aim to be uncomplicated and solution-oriented. The small pipe in our logo is also related to the word solve. So we need a new business card design, which is simple, eye catching and something non traditional (I would probably prefer a square shaped design rather than a rectangle, but open for suggestions). Attached our logo.

Target Market(s)

Usually our customers are Tier1 Telecoms providers (Q-Netra, Palorix, etc) and their executives.

Industry/Entity Type

Business

Contact Information for Business Card

Name: Bence Tolnavari
Email: b.tolnavari@quindor.hu
Web: www.quindor.hu
Mobile: +36 30 518 2769
Title: Managing Director

Optional:
Company name: Quindor and Partners Ltd.
Address: 1087 Budapest, Tolvenka str. 28/C, Hungary

Font styles to use
Other font styles liked:
• helveticaneue_medium, Prime Regular are used now.

Colors

Designer to choose colors to be used in the design.

Requirements
Must have
• I would like to have a 2 sided design.
Nice to have
• I thought if we make the logo a bit bigger (without the company name), that could go to the back with the company name below. I though, if the pipe in the logo is somehow touchable on the business card, would be nice and unique.

```html
<!DOCTYPE html>
<html lang="en">
<head>
<meta charset="utf-8">
<title>Quindor and Partners – Business Card</title>
<link rel="stylesheet" href="https://fonts.googleapis.com/css2?family=Open+Sans:wght@400;600;700&display=swap">
<style>
  :root {
    --backdrop: #2a2a2c;
    --card: #141416;
    --card-edge: #232326;
    --text: #d9d9db;
    --text-soft: #b9b9bc;
    --accent-blue: #1ba4e2;
    --accent-magenta: #d22a8f;
    --mark-grey: #626266;
    --rule: #3a3a3e;
  }
  * { box-sizing: border-box; margin: 0; padding: 0; }
  html, body { width: 1200px; height: 900px; overflow: hidden; }
  body {
    background: var(--backdrop);
    font-family: "Open Sans", Arial, sans-serif;
    display: flex;
    align-items: center;
    justify-content: center;
    gap: 48px;
  }
  .card {
    position: relative;
    width: 520px;
    height: 300px;
    background: var(--card);
    border: 1px solid var(--card-edge);
    border-radius: 24px;
    box-shadow: 0 18px 40px rgba(0,0,0,.45);
    color: var(--text);
  }
  .wordmark {
    font-weight: 400;
    color: var(--mark-grey);
    letter-spacing: .5px;
    white-space: nowrap;
  }
  /* Front */
  .card-front .wordmark {
    position: absolute;
    top: 48px;
    right: 40px;
    font-size: 34px;
  }
  .card-front .divider {
    position: absolute;
    top: 138px;
    left: 40px;
    right: 40px;
    height: 1px;
    background: linear-gradient(90deg, transparent, var(--rule) 30%, var(--rule));
  }
  .person {
    position: absolute;
    left: 40px;
    top: 162px;
  }
  .person-name {
    font-size: 19px;
    font-weight: 700;
    color: #ffffff;
    line-height: 1.2;
  }
  .person-name .surname { color: var(--accent-blue); }
  .person-title {
    font-size: 14px;
    color: var(--text-soft);
    margin-top: 2px;
  }
  .contacts {
    list-style: none;
    margin-top: 12px;
    font-size: 14px;
    line-height: 21px;
  }
  .contacts li { display: flex; align-items: center; gap: 9px; }
  .contacts svg { width: 12px; height: 12px; fill: var(--accent-blue); flex: none; }
  .address {
    position: absolute;
    right: 40px;
    top: 158px;
    text-align: right;
    font-size: 14px;
    line-height: 20px;
    color: var(--text-soft);
    font-style: normal;
  }
  /* Back */
  .card-back {
    display: flex;
    align-items: center;
    justify-content: center;
  }
  .card-back .wordmark { font-size: 38px; }
</style>
</head>
<body>
  <section class="card card-front" aria-label="Business card front">
    <div class="wordmark">Quindor &amp; Partners</div>
    <div class="divider"></div>
    <div class="person">
      <p class="person-name">Bence <span class="surname">Tolnavari</span></p>
      <p class="person-title">Managing Director</p>
      <ul class="contacts">
        <li>
          <svg viewBox="0 0 12 12" aria-hidden="true"><path d="M2.4 0.6l2 2.2-1 1.3c.6 1.5 1.9 2.9 3.5 3.6l1.3-1 2.2 2-1 2c-4.8-.3-8.4-3.9-8.8-8.8z"/></svg>
          +36 30 518 2769
        </li>
        <li>
          <svg viewBox="0 0 12 12" aria-hidden="true"><path d="M0.5 2.5h11v7h-11z M1 3l5 3.6L11 3" fill="var(--accent-blue)"/><path d="M1 3.2l5 3.4 5-3.4" stroke="#141416" stroke-width="1" fill="none"/></svg>
          b.tolnavari@quindor.hu
        </li>
        <li>
          <svg viewBox="0 0 12 12" aria-hidden="true"><circle cx="6" cy="6" r="5.5"/><path d="M0.5 6h11M6 0.5c-2.5 3-2.5 8 0 11M6 0.5c2.5 3 2.5 8 0 11" stroke="#141416" stroke-width=".9" fill="none"/></svg>
          www.quindor.hu
        </li>
      </ul>
    </div>
    <address class="address">
      1087 Budapest<br>
      Tolvenka str.<br>
      28/C, Hungary
    </address>
  </section>

  <section class="card card-back" aria-label="Business card back">
    <div class="wordmark">Quindor &amp; Partners</div>
  </section>
</body>
</html>
```